Hemp company needs website/online store

We are a startup hemp company and we need an online storefront designed. We are very open do design, but will include our logo to help. We make 100% hemp derived products like edibles, concentrates, vapes and THCA flower. Everything is grown locally, and all products are extracted and made in house.

• I would like to highlight that we have Cannabis products that are hemp derived and 100% legal across the US. Also that all cannabis is locally grown and products are extracted and made in house and sent out for third party lab testing.

```html
<!DOCTYPE html>
<html lang="en">
<head>
<meta charset="utf-8">
<title>Greenfield Hemp — Hemp Derived Cannabis Products</title>
<link href="https://fonts.googleapis.com/css2?family=Roboto:wght@400;500;700&display=swap" rel="stylesheet">
<style>
:root{
  --green-dark:#2f6a2a;
  --green:#3a7a2e;
  --green-lime:#8db62b;
  --lime-soft:#b9cf7a;
  --text:#1e1e1e;
  --muted:#555;
  --white:#fff;
  --wood:#6b4a32;
}
*{box-sizing:border-box;margin:0;padding:0}
html,body{width:1200px;height:4458px;overflow:hidden}
body{position:relative;font-family:"Roboto",Arial,sans-serif;color:var(--text);background:var(--white)}
.abs{position:absolute}
a{color:inherit;text-decoration:none}

/* top bar + nav */
.topbar{left:0;top:0;width:1200px;height:42px;background:var(--green-dark);color:#fff;font-size:13px}
.topbar .contact{right:150px;top:12px;display:flex;gap:40px}
.topbar b{font-weight:700}
.nav{left:0;top:42px;width:1200px;height:69px;background:#fff;border-bottom:1px solid #e6e6e6}
.brand-tab{left:82px;top:0;width:192px;height:100px;background:#fff;border-radius:96px 96px 0 0}
.brand{left:82px;top:52px;width:192px;text-align:center;font-size:26px;font-weight:700;color:var(--green-dark);line-height:1}
.brand small{display:block;font-size:12px;letter-spacing:6px;color:var(--green-lime);font-weight:700;margin-top:4px}
.menu{left:398px;top:72px;display:flex;gap:31px;font-size:13px;color:#333}
.menu .active{color:var(--green-lime)}
.search{left:782px;top:62px;width:240px;height:36px;border-radius:18px;box-shadow:0 2px 8px rgba(0,0,0,.12);background:#fff;font-size:13px;color:#555;padding:10px 18px}
.search svg{position:absolute;right:16px;top:11px}
.cart{left:1060px;top:68px}
.cart .count{position:absolute;left:10px;top:-8px;width:16px;height:16px;border-radius:50%;background:var(--green-lime);color:#fff;font-size:10px;text-align:center;line-height:16px}

/* hero */
.hero{left:0;top:111px;width:1200px;height:653px;background:var(--green);overflow:hidden}
.hero-photo{left:510px;top:-50px;width:746px;height:746px;border-radius:50%;background:radial-gradient(circle at 45% 45%,#7a4a1c 0 12%,#a4c23d 34%,var(--green-lime) 60%)}
.hero-wood{left:0;top:539px;width:1200px;height:114px;background:linear-gradient(180deg,#8a6446,var(--wood))}
.hero h1{left:111px;top:163px;width:440px;color:#fff;font-size:30px;line-height:39px;font-weight:700}
.hero p{left:109px;top:292px;width:380px;color:#fff;font-size:13.5px;line-height:25px}
.dot-btn{width:36px;height:36px;border-radius:50%;background:#fff;display:flex;align-items:center;justify-content:center;top:476px}
.notch{left:555px;top:700px;width:90px;height:90px;border-radius:50%;background:#fff}
.notch svg{position:absolute;left:36px;top:22px}

/* section headings */
.h2{left:0;width:1200px;text-align:center;font-size:38px;font-weight:700;color:var(--text)}

/* categories */
.cat{top:940px;width:227px;height:243px;background:#fff;box-shadow:0 2px 12px rgba(0,0,0,.1)}
.cat .img{position:absolute;left:12px;top:9px;width:203px;height:173px;border:1.5px solid var(--lime-soft);border-radius:4px}
.cat .img i{position:absolute;inset:20px 30px;border-radius:40%}
.cat span{position:absolute;left:0;bottom:20px;width:100%;text-align:center;font-size:17px;font-weight:500}

/* featured */
.featured{left:0;top:1287px;width:1200px;height:741px;background:linear-gradient(180deg,var(--green) 0%,#5a9330 55%,var(--green-lime) 100%)}
.featured .h2{color:#fff;top:87px}
.prod{top:164px;width:297px;height:459px;background:#fff;border-radius:4px;text-align:center}
.prod .name{margin-top:28px;font-size:18px;font-weight:700}
.prod .sub{font-size:13px;color:var(--muted);margin-top:8px}
.prod hr{border:0;border-top:1px solid #e3e3e3;margin:18px 0 0}
.prod .price{font-size:29px;font-weight:700;color:var(--green-dark);margin-top:20px}
.prod .ship{font-size:13px;color:var(--green-lime);margin-top:4px}
.prod .pimg{width:190px;height:140px;margin:18px auto 0;border-radius:40%}
.prod .order{display:inline-block;margin-top:26px;width:152px;height:38px;line-height:38px;border-radius:19px;background:var(--green-dark);color:#fff;font-size:13px}
.prod .foot{font-size:13px;color:var(--muted);margin-top:14px}
.arrow{position:absolute}

/* benefits */
.benefit{width:260px}
.benefit h3{font-size:21px;font-weight:700}
.benefit p{font-size:13px;color:var(--muted);line-height:21px;margin-top:6px}
.benefit.left{text-align:right;left:8px}
.benefit.right{left:932px}
.bdot{width:11px;height:11px;border-radius:50%;background:var(--green-dark)}
.bline{background:#8a8a8a}
.mark{left:469px;top:2282px;width:260px;height:260px;border-radius:50%;background:#eef4e2;display:flex;align-items:center;justify-content:center;font-size:26px;font-weight:700;color:var(--green-dark)}

/* who we are */
.who-band{left:433px;top:2788px;width:767px;height:598px;background:var(--green-dark)}
.who-ring{left:-14px;top:2767px;width:642px;height:642px;border-radius:50%;background:#fff}
.who-photo{left:0;top:2781px;width:614px;height:614px;border-radius:50%;background:radial-gradient(circle at 50% 55%,#8a3a1e 0,#5f6a28 35%,#2e4a22 65%,#16241a 100%)}
.who h2{left:681px;top:2880px;color:#fff;font-size:38px;font-weight:700}
.who p{left:681px;top:2932px;width:411px;color:#fff;font-size:13.5px;line-height:21.5px;text-align:justify}
.who .btn{left:684px;top:3251px;width:150px;height:38px;border-radius:19px;background:var(--green-lime);color:#fff;font-size:13px;font-weight:700;text-align:center;line-height:38px}

/* testimonials */
.testi{top:3611px;width:465px;height:320px;background:#fff;box-shadow:0 2px 14px rgba(0,0,0,.1)}
.testi .frame{position:absolute;left:16px;top:16px;right:16px;bottom:16px;border:1.5px solid var(--lime-soft);border-radius:12px}
.testi .quote{position:absolute;left:200px;top:-6px;font-size:90px;font-weight:700;color:var(--green-dark);line-height:1;font-family:Georgia,serif}
.testi p{position:absolute;left:60px;top:68px;width:345px;text-align:center;font-size:12.5px;line-height:21px;color:#444}
.testi .avatar{position:absolute;left:193px;top:147px;width:80px;height:80px;border-radius:50%;background:radial-gradient(circle,#a77a5c,#5a4030)}
.testi .who-name{position:absolute;left:0;width:100%;top:244px;text-align:center;font-size:19px;font-weight:500}

/* footer */
.footer{left:0;top:4049px;width:1200px;height:409px;background:var(--green-dark);color:#fff}
.footer .flogo{left:109px;top:168px;font-size:36px;font-weight:700;line-height:1}
.footer .flogo small{display:block;font-size:15px;letter-spacing:10px;text-align:right;margin-top:4px}
.footer h4{font-size:19px;font-weight:700}
.footer ul{list-style:none;font-size:13.5px;line-height:26px}
.footer .field{left:802px;top:164px;width:286px;height:51px;border-radius:26px;border:1px solid rgba(255,255,255,.3);background:rgba(255,255,255,.08);font-size:13px;color:rgba(255,255,255,.7);padding:16px 26px}
.footer .field svg{position:absolute;right:22px;top:19px}
.copy{left:0;top:351px;width:1200px;text-align:center;font-size:13px}
</style>
</head>
<body>

<!-- header -->
<div class="abs topbar">
  <div class="abs contact"><span>✉ Email : hello@greenfieldhemp.com</span><span>☎ Phone : <b>+1 555 010 2040</b></span></div>
</div>
<div class="abs nav"></div>
<div class="abs brand-tab"></div>
<div class="abs brand">Greenfield<small>HEMP</small></div>
<nav class="abs menu">
  <a class="active">Home</a><a>About</a><a>Products</a><a>Reviews</a><a>Contact</a>
</nav>
<div class="abs search">Search
  <svg width="14" height="14" viewBox="0 0 14 14"><circle cx="6" cy="6" r="4.5" fill="none" stroke="#2f6a2a" stroke-width="2"/><path d="M9.5 9.5L13 13" stroke="#2f6a2a" stroke-width="2"/></svg>
</div>
<div class="abs cart">
  <svg width="20" height="20" viewBox="0 0 20 20"><path d="M3 6h14l-1.5 12h-11z" fill="none" stroke="#777" stroke-width="1.5"/><path d="M7 8V5a3 3 0 0 1 6 0v3" fill="none" stroke="#777" stroke-width="1.5"/></svg>
  <span class="count">0</span>
</div>

<!-- hero -->
<section class="abs hero">
  <div class="abs hero-wood"></div>
  <div class="abs hero-photo" role="img" aria-label="Amber tincture bottles with droppers among fresh hemp leaves"></div>
  <h1 class="abs">We have Cannabis products that are hemp derived and 100% legal across the US</h1>
  <p class="abs">Also that all cannabis is locally grown and products are extracted and made in house and sent out for third party lab testing.</p>
  <div class="abs dot-btn" style="left:112px"><svg width="8" height="10" viewBox="0 0 8 10"><path d="M6 1L2 5l4 4" fill="none" stroke="#333" stroke-width="1.5"/></svg></div>
  <div class="abs dot-btn" style="left:155px"><svg width="8" height="10" viewBox="0 0 8 10"><path d="M2 1l4 4-4 4" fill="none" stroke="#333" stroke-width="1.5"/></svg></div>
  <div class="abs notch"><svg width="18" height="22" viewBox="0 0 18 22"><path d="M9 1v19M2 13l7 7 7-7" fill="none" stroke="#222" stroke-width="2"/></svg></div>
</section>

<!-- categories -->
<h2 class="abs h2" style="top:862px">Categories</h2>
<div class="abs cat" style="left:111px"><div class="img"><i role="img" aria-label="Colourful gummy edibles with hemp leaves" style="background:radial-gradient(circle,#f2b43a,#c9432e 55%,#fff 75%)"></i></div><span>Edibles</span></div>
<div class="abs cat" style="left:362px"><div class="img"><i role="img" aria-label="Amber shatter concentrate" style="background:radial-gradient(circle,#f0b24a,#d3641f 55%,#fff 75%)"></i></div><span>Concentrates</span></div>
<div class="abs cat" style="left:611px"><div class="img"><i role="img" aria-label="Vape cartridge" style="background:radial-gradient(ellipse,#caa23a,#6b6f7a 45%,#fff 70%)"></i></div><span>Vapes</span></div>
<div class="abs cat" style="left:861px"><div class="img"><i role="img" aria-label="THCA flower bud" style="background:radial-gradient(circle,#8a8a4c,#5a5a32 50%,#fff 72%)"></i></div><span>THCA flowers</span></div>

<!-- featured -->
<section class="abs featured">
  <h2 class="abs h2">Featured Products</h2>
  <svg class="arrow" style="left:49px;top:384px" width="12" height="20" viewBox="0 0 12 20"><path d="M10 2L2 10l8 8" fill="none" stroke="#fff" stroke-width="2"/></svg>
  <svg class="arrow" style="left:1137px;top:384px" width="12" height="20" viewBox="0 0 12 20"><path d="M2 2l8 8-8 8" fill="none" stroke="#fff" stroke-width="2"/></svg>
  <div class="abs prod" style="left:111px">
    <div class="name">Product 01</div><div class="sub">Lorem ipsum dolor sit amet</div><hr>
    <div class="price">$25.00</div><div class="ship">FREE SHIPPING</div>
    <div class="pimg" role="img" aria-label="Gummy edibles with hemp leaf" style="background:radial-gradient(circle,#f2b43a,#d04a2e 50%,#fff 72%)"></div>
    <a class="order">ORDER NOW</a><div class="foot">Lorem ipsum dolor sit amet</div>
  </div>
  <div class="abs prod" style="left:452px">
    <div class="name">Product 01</div><div class="sub">Lorem ipsum dolor sit amet</div><hr>
    <div class="price">$25.00</div><div class="ship">FREE SHIPPING</div>
    <div class="pimg" role="img" aria-label="Vape cartridge" style="background:radial-gradient(ellipse,#d9a42e,#555 40%,#fff 68%)"></div>
    <a class="order">ORDER NOW</a><div class="foot">Lorem ipsum dolor sit amet</div>
  </div>
  <div class="abs prod" style="left:791px">
    <div class="name">Product 01</div><div class="sub">Lorem ipsum dolor sit amet</div><hr>
    <div class="price">$25.00</div><div class="ship">FREE SHIPPING</div>
    <div class="pimg" role="img" aria-label="Blue glass hand pipe" style="background:radial-gradient(ellipse 30% 50%,#2f7fc0,#1c4a86 60%,#fff 100%)"></div>
    <a class="order">ORDER NOW</a><div class="foot">Lorem ipsum dolor sit amet</div>
  </div>
</section>

<!-- benefits -->
<h2 class="abs h2" style="top:2124px">Our Benefits</h2>
<div class="abs benefit left" style="top:2184px"><h3>Lorem ipsum dolor</h3><p>Lorem ipsum dolor sit amet, cons<br>ectetur adipiscing elit</p></div>
<div class="abs benefit left" style="top:2394px"><h3>Lorem ipsum dolor</h3><p>Lorem ipsum dolor sit amet, cons<br>ectetur adipiscing elit</p></div>
<div class="abs benefit left" style="top:2604px"><h3>Lorem ipsum dolor</h3><p>Lorem ipsum dolor sit amet, cons<br>ectetur adipiscing elit</p></div>
<div class="abs benefit right" style="top:2184px"><h3>Lorem ipsum dolor</h3><p>Lorem ipsum dolor sit amet, cons<br>ectetur adipiscing elit</p></div>
<div class="abs benefit right" style="top:2394px"><h3>Lorem ipsum dolor</h3><p>Lorem ipsum dolor sit amet, cons<br>ectetur adipiscing elit</p></div>
<div class="abs benefit right" style="top:2604px"><h3>Lorem ipsum dolor</h3><p>Lorem ipsum dolor sit amet, cons<br>ectetur adipiscing elit</p></div>

<div class="abs bdot" style="left:289px;top:2194px"></div>
<div class="abs bdot" style="left:289px;top:2404px"></div>
<div class="abs bdot" style="left:289px;top:2614px"></div>
<div class="abs bline" style="left:300px;top:2199px;width:64px;height:1px"></div>
<div class="abs bline" style="left:300px;top:2409px;width:133px;height:1px"></div>
<div class="abs bline" style="left:300px;top:2619px;width:64px;height:1px"></div>
<div class="abs bline" style="left:364px;top:2199px;width:1px;height:420px"></div>

<div class="abs bdot" style="left:898px;top:2194px"></div>
<div class="abs bdot" style="left:898px;top:2404px"></div>
<div class="abs bdot" style="left:898px;top:2614px"></div>
<div class="abs bline" style="left:834px;top:2199px;width:64px;height:1px"></div>
<div class="abs bline" style="left:765px;top:2409px;width:133px;height:1px"></div>
<div class="abs bline" style="left:834px;top:2619px;width:64px;height:1px"></div>
<div class="abs bline" style="left:834px;top:2199px;width:1px;height:420px"></div>

<div class="abs mark">Greenfield</div>

<!-- who we are -->
<div class="abs who-band"></div>
<div class="abs who-ring"></div>
<div class="abs who-photo" role="img" aria-label="Close-up of colourful gummy edibles"></div>
<section class="who">
  <h2 class="abs">Who We Are</h2>
  <p class="abs">Lorem ipsum dolor sit amet, consectetur adipiscing elit, sed do eiusmod tempor incididunt ut labore et dolore magna aliqua. Ut enim ad minim veniam, quis nostrud exercitation ullamco laboris nisi ut aliquip ex ea commodo consequat. Duis aute irure dolor in reprehenderit in voluptate velit esse cillum dolore eu fugiat nulla pariatur. Excepteur sint occaecat cupidatat non proident, sunt in culpa qui officia deserunt mollit anim id est laborum. Lorem ipsum dolor sit amet, consectetur adipiscing elit, sed do eiusmod tempor incididunt ut labore et dolore magna aliqua. Ut enim ad minim veniam, quis nostrud exercitation ullamco laboris nisi ut aliquip ex ea commodo consequat. Duis aute irure dolor in reprehenderit in voluptate velit esse cillum dolore eu fugiat nulla pariatur. Excepteur sint occaecat cupidatat non proident, sunt in culpa qui officia deserunt mollit anim id est laborum.</p>
  <a class="abs btn">READ MORE</a>
</section>

<!-- testimonials -->
<h2 class="abs h2" style="top:3502px">What Our Client Says</h2>
<svg class="arrow" style="left:49px;top:3774px" width="12" height="20" viewBox="0 0 12 20"><path d="M10 2L2 10l8 8" fill="none" stroke="#333" stroke-width="2"/></svg>
<svg class="arrow" style="left:1137px;top:3774px" width="12" height="20" viewBox="0 0 12 20"><path d="M2 2l8 8-8 8" fill="none" stroke="#333" stroke-width="2"/></svg>
<div class="abs testi" style="left:111px">
  <div class="frame"></div><div class="quote">“</div>
  <p>Lorem ipsum dolor sit amet, consectetur adipiscing elit, sed do eiusmod tempor incididunt ut labore et dolore magna aliqua. Ut enim ad minim veniam, quis nostrud exercitation nisi ut aliquip ex ea commodo consequat.</p>
  <div class="avatar" role="img" aria-label="Customer portrait"></div>
  <div class="who-name">John Doe</div>
</div>
<div class="abs testi" style="left:623px">
  <div class="frame"></div><div class="quote">“</div>
  <p>Lorem ipsum dolor sit amet, consectetur adipiscing elit, sed do eiusmod tempor incididunt ut labore et dolore magna aliqua. Ut enim ad minim veniam, quis nostrud exercitation nisi ut aliquip ex ea commodo consequat.</p>
  <div class="avatar" role="img" aria-label="Customer portrait"></div>
  <div class="who-name">John Doe</div>
</div>

<!-- footer -->
<footer class="abs footer">
  <div class="abs flogo">Greenfield<small>HEMP</small></div>
  <h4 class="abs" style="left:441px;top:108px">Quick Links</h4>
  <ul class="abs" style="left:443px;top:158px"><li>Home</li><li>About</li><li>Our Products</li><li>Reviews</li><li>Contact</li></ul>
  <ul class="abs" style="left:615px;top:158px"><li>Contact Us</li><li>Terms of Conditions</li><li>Return &amp; Refunds</li><li>Faq</li><li>Support</li></ul>
  <h4 class="abs" style="left:801px;top:108px">Newsletter</h4>
  <div class="abs field">Email address
    <svg width="14" height="10" viewBox="0 0 14 10"><path d="M0 5h12M8 1l4 4-4 4" fill="none" stroke="#fff" stroke-width="1.6"/></svg>
  </div>
  <div class="abs copy">© Copyrights 2023 | All Rights Reserved</div>
</footer>

</body>
</html>
```